Harrow Grading LLC business card design

Excavation company business cards

Contact Information for Business Card

Harrow Grading LLC cell phone 208-417-6290 office phone 208-319-4856 harrowgradingllc@maplecove.com Driveways, site prep, retaining walls, septic systems, rock delivery

Colors

Designer to choose colors to be used in the design.

```html
<!DOCTYPE html>
<html lang="en">
<head>
<meta charset="utf-8">
<title>Harrow Grading LLC – Business Card</title>
<link rel="stylesheet" href="https://fonts.googleapis.com/css2?family=Work+Sans:wght@400;500;600;700&display=swap">
<style>
  :root {
    --page: #d9d9d9;
    --card-white: #ffffff;
    --brand-orange: #ef6c1f;
    --ink: #4a4a4a;
    --ink-soft: #5e5e5e;
    --steel: #5f5f5f;
    --steel-light: #6c6c6c;
    --stripe: #ffffff;
    --rule: #e2e2e2;
  }
  * { box-sizing: border-box; margin: 0; padding: 0; }
  html, body { width: 1200px; height: 800px; overflow: hidden; }
  body {
    background: var(--page);
    font-family: "Work Sans", Arial, sans-serif;
    position: relative;
  }
  .card {
    position: absolute;
    width: 560px;
    height: 320px;
    box-shadow: 0 10px 28px rgba(0,0,0,0.18);
    overflow: hidden;
  }
  /* Front */
  .card-front { left: 60px; top: 80px; background: var(--card-white); }
  .brand-band {
    position: absolute; left: 0; right: 0; bottom: 0; height: 26px;
    background: var(--steel);
  }
  .brand-band svg { position: absolute; top: 0; height: 26px; width: 60px; }
  .brand-band .stripes-left { left: 14px; }
  .brand-band .stripes-right { right: 14px; }
  .brand-block {
    position: absolute; left: 28px; top: 0; bottom: 26px; width: 236px;
    display: flex; align-items: center; gap: 9px;
  }
  .brand-mark { width: 15px; height: 15px; background: var(--brand-orange); flex: none; }
  .brand-name {
    color: var(--brand-orange); font-weight: 700; font-size: 18px; line-height: 1.1;
    white-space: nowrap;
  }
  .divider { position: absolute; left: 262px; top: 40px; width: 20px; height: 210px; }
  .contact-block { position: absolute; left: 300px; top: 66px; right: 14px; }
  .person-name { color: var(--ink); font-weight: 600; font-size: 26px; letter-spacing: 0.5px; }
  .person-title { color: var(--brand-orange); font-size: 15px; margin: 2px 0 16px; }
  .contact-list { list-style: none; }
  .contact-list li {
    display: flex; align-items: center; gap: 9px;
    color: var(--ink-soft); font-size: 13.5px; line-height: 22px; white-space: nowrap;
  }
  .contact-list svg { width: 12px; height: 12px; flex: none; }
  /* Back */
  .card-back { left: 580px; top: 420px; background: var(--steel); }
  .illustration-area {
    position: absolute; left: 120px; top: 40px; width: 320px; height: 170px;
    background: linear-gradient(180deg, var(--steel-light) 0%, var(--steel) 100%);
    border-radius: 4px;
  }
  .web-address {
    position: absolute; left: 0; right: 0; bottom: 52px; text-align: center;
    color: #f2f2f2; font-size: 15px; font-weight: 500; letter-spacing: 3.5px;
  }
</style>
</head>
<body>
  <section class="card card-front" aria-label="Business card front">
    <div class="brand-block">
      <span class="brand-mark"></span>
      <span class="brand-name">Harrow Grading LLC</span>
    </div>
    <svg class="divider" viewBox="0 0 20 210" aria-hidden="true">
      <line x1="2" y1="0" x2="18" y2="210" stroke="var(--rule)" stroke-width="1.5"/>
    </svg>
    <div class="contact-block">
      <h1 class="person-name">Daniel Reyes</h1>
      <p class="person-title">President</p>
      <ul class="contact-list">
        <li><svg viewBox="0 0 12 12"><path d="M3 1 L5 3.5 L4 5 Q5 7 7 8 L8.5 7 L11 9 L9.5 11 Q4 10.5 1 3 Z" fill="var(--brand-orange)"/></svg>208-319-4856</li>
        <li><svg viewBox="0 0 12 12"><rect x="3" y="1" width="6" height="10" rx="1" fill="none" stroke="var(--ink-soft)" stroke-width="1.3"/></svg>208-417-6290</li>
        <li><svg viewBox="0 0 12 12"><rect x="1" y="2.5" width="10" height="7" fill="var(--brand-orange)"/><path d="M1 2.5 L6 6.5 L11 2.5" fill="none" stroke="#fff" stroke-width="1"/></svg>harrowgradingllc@maplecove.com</li>
        <li><svg viewBox="0 0 12 12"><circle cx="6" cy="6" r="5" fill="var(--brand-orange)"/><path d="M3 6 H9 M6 1.5 Q3.5 6 6 10.5 M6 1.5 Q8.5 6 6 10.5" stroke="#fff" stroke-width="0.8" fill="none"/></svg>harrowgradingllc.com</li>
      </ul>
    </div>
    <div class="brand-band">
      <svg class="stripes-left" viewBox="0 0 60 26" aria-hidden="true">
        <path d="M8 26 L16 0 H21 L13 26 Z M22 26 L30 0 H35 L27 26 Z M36 26 L44 0 H49 L41 26 Z" fill="var(--stripe)"/>
      </svg>
      <svg class="stripes-right" viewBox="0 0 60 26" aria-hidden="true">
        <path d="M8 26 L16 0 H21 L13 26 Z M22 26 L30 0 H35 L27 26 Z M36 26 L44 0 H49 L41 26 Z" fill="var(--stripe)"/>
      </svg>
    </div>
  </section>

  <section class="card card-back" aria-label="Business card back">
    <div class="illustration-area" role="img" aria-label="Embossed silver illustration of an excavator in front of mountain peaks"></div>
    <p class="web-address">WWW.HARROWGRADINGLLC.COM</p>
  </section>
</body>
</html>
```